Coastline Premier Retreats Business Card Design

Design a business card for Coastline Premier Retreats. Look at the website for colors and reference. Card should have logo, name, title, office number, mobile number, email, URL and a tagline like, "Luxury Hotel & Resort Email Marketing" (This might change).

https://www.coastlinepremierretreats.example

The rest I will leave up to your imagination.

Contact Information for Business Card

Logo, name, title, office number, mobile number, email, URL and a tagline like, "Luxury Hotel & Resort Email Marketing" (This might change).

```html
<!DOCTYPE html>
<html lang="en">
<head>
<meta charset="utf-8">
<title>Coastline Premier Retreats — Business Card</title>
<link href="https://fonts.googleapis.com/css2?family=Lato:wght@400;700&family=Dancing+Script:wght@500&display=swap" rel="stylesheet">
<style>
  :root {
    --backdrop: #2b2b2b;
    --card: #1d1d1d;
    --accent: #ff7a00;
    --silver: #c9c9c9;
    --text: #d4d4d4;
    --muted: #5a5a5a;
  }
  * { box-sizing: border-box; margin: 0; padding: 0; }
  html, body { width: 1200px; height: 689px; overflow: hidden; }
  body {
    background: var(--backdrop);
    font-family: "Lato", Arial, sans-serif;
    display: flex;
    align-items: center;
    justify-content: center;
    gap: 60px;
  }
  .card {
    width: 520px;
    height: 297px;
    background: var(--card);
    position: relative;
    box-shadow: 0 18px 40px rgba(0,0,0,.45);
  }
  /* Front */
  .card-front {
    display: flex;
    flex-direction: column;
    align-items: center;
    justify-content: center;
    gap: 26px;
  }
  .brand {
    display: flex;
    align-items: center;
    gap: 14px;
  }
  .brand-square {
    width: 18px;
    height: 18px;
    background: var(--accent);
  }
  .brand-name {
    font-weight: 700;
    font-size: 27px;
    letter-spacing: 1.5px;
    text-transform: uppercase;
    color: var(--silver);
  }
  .tagline {
    font-family: "Dancing Script", cursive;
    font-size: 26px;
    color: #f2f2f2;
  }
  /* Back */
  .card-back .frame {
    position: absolute;
    inset: 18px;
    border: 1.5px solid var(--accent);
  }
  .card-back .content {
    position: absolute;
    inset: 18px;
    display: flex;
    align-items: center;
    padding: 0 26px 0 44px;
  }
  .person { flex: 0 0 170px; }
  .person-name {
    font-size: 27px;
    font-weight: 400;
    letter-spacing: 1px;
    text-transform: uppercase;
    color: #bdbdbd;
    line-height: 1.1;
  }
  .person-title {
    font-size: 15px;
    color: var(--accent);
    margin-top: 2px;
  }
  .divider {
    width: 1px;
    height: 130px;
    background: var(--muted);
    margin: 0 22px 0 10px;
  }
  .contacts {
    list-style: none;
    font-size: 12.5px;
    color: var(--text);
    line-height: 1.45;
  }
  .contacts li {
    display: flex;
    align-items: flex-start;
    gap: 9px;
    margin-bottom: 2px;
  }
  .contacts svg {
    width: 11px;
    height: 11px;
    flex: 0 0 11px;
    margin-top: 4px;
    fill: var(--accent);
  }
</style>
</head>
<body>
  <section class="card card-front">
    <div class="brand">
      <span class="brand-square"></span>
      <span class="brand-name">Coastline Premier Retreats</span>
    </div>
    <p class="tagline">Luxury Hotel &amp; Resort Email Marketing</p>
  </section>

  <section class="card card-back">
    <div class="frame"></div>
    <div class="content">
      <div class="person">
        <h1 class="person-name">Daniel Reyes</h1>
        <p class="person-title">Founder &amp; CEO</p>
      </div>
      <div class="divider"></div>
      <ul class="contacts">
        <li>
          <svg viewBox="0 0 12 12"><path d="M6 0a4 4 0 0 0-4 4c0 3 4 8 4 8s4-5 4-8a4 4 0 0 0-4-4zm0 5.5A1.5 1.5 0 1 1 6 2.5a1.5 1.5 0 0 1 0 3z"/></svg>
          <span>418 Harbor View Lane<br>Seabrook, ME 04901</span>
        </li>
        <li>
          <svg viewBox="0 0 12 12"><path d="M2.5 0.5l2 2.5-1 1.5c.7 1.6 2 2.9 3.6 3.6l1.4-1 2.5 2-1.2 2.2C4.8 11 1 7.2.3 1.7z"/></svg>
          <span>(555) 014-2290</span>
        </li>
        <li>
          <svg viewBox="0 0 12 12"><path d="M3 0h6a1 1 0 0 1 1 1v10a1 1 0 0 1-1 1H3a1 1 0 0 1-1-1V1a1 1 0 0 1 1-1zm.5 1.5v8h5v-8zM6 10.2a.6.6 0 1 0 0 1.2.6.6 0 0 0 0-1.2z"/></svg>
          <span>(555) 014-3371</span>
        </li>
        <li>
          <svg viewBox="0 0 12 12"><path d="M0 2h12v1L6 7 0 3zM0 4.2l6 4 6-4V10H0z"/></svg>
          <span>info@coastlinepremierretreats.example</span>
        </li>
        <li>
          <svg viewBox="0 0 12 12"><circle cx="6" cy="6" r="5.5"/><path d="M.5 6h11M6 .5c-2 2-2 9 0 11M6 .5c2 2 2 9 0 11" stroke="#1d1d1d" stroke-width=".9" fill="none"/></svg>
          <span>coastlinepremierretreats.example</span>
        </li>
      </ul>
    </div>
  </section>
</body>
</html>
```